I'm looking for a smart new design for business cards

Industry/Entity Type

Commercial Electrical

Contact Information for Business Card

Logo, name, email, position, website QR

Requirements
Nice to have
• Logo embedded behind the text side

```html
<!DOCTYPE html>
<html lang="en">
<head>
<meta charset="UTF-8">
<title>Voltmark Commercial Electric — Business Card</title>
<link href="https://fonts.googleapis.com/css2?family=Montserrat:wght@600;700;800&family=Arimo:wght@400&display=swap" rel="stylesheet">
<style>
  :root {
    --paper-bg: #e6e6e6;
    --card-white: #ffffff;
    --navy: #161a8c;
    --brand-red: #e3143a;
    --ink: #111111;
    --body-grey: #4a4a4a;
    --rule-grey: #b9b9b9;
    --back-dark: #0a0d6e;
    --back-mid: #1219a8;
    --back-bright: #1d2ef0;
  }
  * { margin: 0; padding: 0; box-sizing: border-box; }
  html, body { width: 1200px; height: 1200px; overflow: hidden; }
  body { background: var(--paper-bg); position: relative; font-family: "Arimo", Arial, sans-serif; }

  .card { position: absolute; width: 688px; height: 393px; border-radius: 24px; overflow: hidden; }
  .card--front { left: 267px; top: 159px; background: var(--card-white); }
  .card--back { left: 262px; top: 654px; }

  .brand-block { position: absolute; left: 66px; top: 130px; width: 280px; text-align: center; }
  .brand-name { display: inline-flex; align-items: center; gap: 10px;
    font-family: "Montserrat", sans-serif; font-weight: 800; font-size: 40px; letter-spacing: 1px; color: var(--navy); line-height: 1; }
  .brand-dot { width: 16px; height: 16px; border-radius: 50%; background: var(--brand-red); }
  .brand-tagline { margin-top: 22px; font-family: "Montserrat", sans-serif; font-weight: 700; font-size: 15.5px;
    color: var(--ink); line-height: 19px; letter-spacing: 0.2px; }

  .divider { position: absolute; left: 362px; top: 86px; width: 1.5px; height: 227px; background: var(--rule-grey); }

  .contact { position: absolute; left: 387px; top: 92px; }
  .person-name { font-family: "Montserrat", sans-serif; font-weight: 800; font-size: 26px; color: var(--navy); letter-spacing: 0.5px; line-height: 1.1; }
  .person-role { font-size: 15px; color: var(--brand-red); margin-top: 3px; }
  .address { margin-top: 19px; font-size: 16px; line-height: 21px; color: var(--body-grey); }
  .contact-list { list-style: none; margin-top: 11px; }
  .contact-list li { display: flex; align-items: center; height: 20.5px; font-size: 16px; color: var(--body-grey); }
  .contact-list svg { width: 14px; height: 14px; margin-right: 11px; flex: none; fill: var(--brand-red); }

  .back-pattern { position: absolute; inset: 0;
    background: linear-gradient(90deg, var(--back-dark) 0%, var(--back-mid) 50%, var(--back-bright) 100%); }
  .back-brand { position: absolute; left: 514px; top: 290px; display: flex; align-items: center; gap: 7px;
    font-family: "Montserrat", sans-serif; font-weight: 800; font-size: 22px; color: var(--card-white); letter-spacing: 0.5px; line-height: 1; }
  .back-brand .brand-square { width: 10px; height: 10px; background: var(--brand-red); }
</style>
</head>
<body>
  <section class="card card--front" aria-label="Business card front">
    <div class="brand-block">
      <div class="brand-name"><span class="brand-dot"></span>VOLTMARK</div>
      <p class="brand-tagline">VOLTMARK COMMERCIAL<br>ELECTRIC</p>
    </div>
    <div class="divider"></div>
    <div class="contact">
      <h1 class="person-name">DANIEL REEVE</h1>
      <p class="person-role">President</p>
      <p class="address">5218 Juniper Street<br>Westfield, Canada 48210</p>
      <ul class="contact-list">
        <li><svg viewBox="0 0 24 24"><path d="M6.6 10.8a15.1 15.1 0 0 0 6.6 6.6l2.2-2.2c.3-.3.7-.4 1-.2 1.1.4 2.3.6 3.6.6.6 0 1 .4 1 1V20c0 .6-.4 1-1 1A17 17 0 0 1 3 4c0-.6.4-1 1-1h3.5c.6 0 1 .4 1 1 0 1.3.2 2.5.6 3.6.1.3 0 .7-.2 1z"/></svg>555-201-4830</li>
        <li><svg viewBox="0 0 24 24"><path d="M7 1h10a2 2 0 0 1 2 2v18a2 2 0 0 1-2 2H7a2 2 0 0 1-2-2V3a2 2 0 0 1 2-2zm0 3v14h10V4zm5 15.5a1 1 0 1 0 0 2 1 1 0 0 0 0-2z"/></svg>555-201-4871</li>
        <li><svg viewBox="0 0 24 24"><path d="M2 5h20v14H2zm2 2v.5l8 5.5 8-5.5V7zm0 2.9V17h16V9.9l-8 5.5z"/></svg>info@voltmark.com</li>
        <li><svg viewBox="0 0 24 24"><path d="M12 2a10 10 0 1 0 0 20 10 10 0 0 0 0-20zm-1 17.9A8 8 0 0 1 4.2 10.2L9 15v1a2 2 0 0 0 2 2zm6.9-2.5A2 2 0 0 0 16 16h-1v-3a1 1 0 0 0-1-1H8v-2h2a1 1 0 0 0 1-1V7h2a2 2 0 0 0 2-2v-.4a8 8 0 0 1 2.9 12.8z"/></svg>www.voltmark.com</li>
      </ul>
    </div>
  </section>

  <section class="card card--back" aria-label="Business card back">
    <div class="back-pattern" role="img" aria-label="Repeating tonal brand pattern in deep blues, fading from dark navy to bright blue"></div>
    <div class="back-brand"><span class="brand-square"></span>VOLTMARK</div>
  </section>
</body>
</html>
```